Realty Group Needs Classy, Contemporary Letterhead Design

We need a letterhead design for a new realty company located in NY, USA. We buy investment properties to rehabilitate and or keep in our rental portfolio.

```html
<!DOCTYPE html>
<html lang="en">
<head>
<meta charset="utf-8">
<title>Halvern Realty Group – Letterhead</title>
<link href="https://fonts.googleapis.com/css2?family=Lato:wght@400&family=Open+Sans:wght@400&display=swap" rel="stylesheet">
<style>
  :root {
    --brand-purple: #522a86;
    --accent-gray: #7f7f7f;
    --text-dark: #3c3c3c;
    --text-mid: #555555;
    --page-white: #ffffff;
    --backdrop: #dcdcdc;
  }
  * { box-sizing: border-box; margin: 0; padding: 0; }
  html, body { width: 1040px; height: 1200px; overflow: hidden; }
  body { background: var(--backdrop); position: relative; }

  .letterhead {
    position: absolute; left: 70px; top: 21px;
    width: 900px; height: 1158px;
    background: var(--page-white);
    box-shadow: 0 4px 18px rgba(0,0,0,0.25);
    font-family: "Open Sans", Arial, sans-serif;
    color: var(--text-mid);
    overflow: hidden;
  }
  .header-wave { position: absolute; left: 0; top: 0; width: 900px; height: 160px; display: block; }

  .company-name {
    position: absolute; left: 85px; top: 88px;
    font-family: "Open Sans", Arial, sans-serif; font-weight: 400;
    font-size: 22px; line-height: 30px; color: var(--brand-purple);
  }

  .letter-body { position: absolute; left: 85px; width: 727px; font-size: 14.2px; line-height: 26px; }
  .issue-date { top: 228px; }
  .recipient { top: 262px; line-height: 17.5px; }
  .salutation { top: 360px; }
  .body-copy { top: 411px; text-align: justify; hyphens: auto; -webkit-hyphens: auto; }
  .body-copy p + p { margin-top: 26px; }
  .closing { top: 802px; }

  .signature { position: absolute; left: 85px; top: 840px; width: 210px; height: 26px;
    background: linear-gradient(90deg, rgba(80,80,80,0.18), rgba(80,80,80,0.05)); border-radius: 3px; }
  .signer-name { position: absolute; left: 85px; top: 877px; font-size: 18px; color: var(--text-dark); }
  .signer-title { position: absolute; left: 85px; top: 907px; font-size: 14.2px; }

  .contact-bar { position: absolute; left: 0; top: 1019px; width: 18px; height: 64px; background: var(--accent-gray); }
  .contact-list { position: absolute; left: 42px; top: 1020px; list-style: none;
    font-family: "Lato", Arial, sans-serif; font-size: 17px; line-height: 21px; color: #222; }
  .contact-list li { display: flex; align-items: center; gap: 9px; }
  .contact-list svg { width: 16px; height: 16px; fill: var(--brand-purple); flex: none; }

  .footer-band { position: absolute; left: 0; bottom: 0; width: 900px; height: 41px;
    background: var(--brand-purple); color: #fff; text-align: center;
    font-family: "Lato", Arial, sans-serif; font-size: 17px; line-height: 41px; }
</style>
</head>
<body>
  <main class="letterhead">
    <svg class="header-wave" viewBox="0 0 900 160" aria-hidden="true">
      <rect width="900" height="160" fill="var(--brand-purple)"/>
      <path d="M0,118 C40,60 130,16 260,16 C450,16 700,62 900,110 L900,160 L0,160 Z" fill="var(--accent-gray)"/>
      <path d="M0,133 C40,72 130,22 260,22 C450,22 700,74 900,128 L900,160 L0,160 Z" fill="var(--page-white)"/>
    </svg>

    <p class="company-name">Halvern Realty Group, LLC</p>

    <p class="letter-body issue-date">Issuing Date: May 5, 2018</p>
    <p class="letter-body recipient">Name Of Employee Mr. XYZABC<br>Address of Employee<br>Address Line 2 etc..</p>
    <p class="letter-body salutation">Dear Mr.XYZABC</p>

    <div class="letter-body body-copy">
      <p>Lorem Ipsum has been the industry's standard dummy text ever since the 1500s, when an unknown printer took a galley of type and scrambled it to make a type specimen book. It has survived not only five centuries, but also the leap into electronic typesetting, remaining essentially unchanged. It was popularised in the 1960s with the release of Letraset sheets containing Lorem Ipsum passages, and more recently with desktop publishing software like Aldus PageMaker including versions of Lorem Ipsum.</p>
      <p>Lorem Ipsum is simply dummy text of the printing and typesetting industry. Lorem Ipsum has been the industry's standard dummy text ever since the 1500s, when an unknown printer took a galley of type and scrambled it to make a type specimen book.</p>
      <p>It has survived not only five centuries, but also the leap into electronic typesetting, remaining essentially unchanged. It was popularised in the 1960s with the release of Letraset sheets containing Lorem IpsumIpsum passages.</p>
    </div>

    <p class="letter-body closing">Yours Sincerely</p>
    <div class="signature" role="img" aria-label="Handwritten signature of Daniel Marlowe"></div>
    <p class="signer-name">Daniel Marlowe</p>
    <p class="signer-title">Managing Director</p>

    <div class="contact-bar"></div>
    <ul class="contact-list">
      <li><svg viewBox="0 0 16 16" aria-hidden="true"><path d="M2 6c0-2 2-3 6-3s6 1 6 3v1h-3V5.5H5V7H2z M4 8h8l1.5 5h-11z"/></svg>044-555 010 234</li>
      <li><svg viewBox="0 0 16 16" aria-hidden="true"><path d="M1 3h14v10H1z M2 4l6 5 6-5" stroke="#fff" stroke-width="1.2"/></svg>info@halvernrealty.com</li>
      <li><svg viewBox="0 0 16 16" aria-hidden="true"><circle cx="8" cy="8" r="7"/><path d="M5 4c2 1 1 3 3 3s1 3 3 4M9 2c0 2 3 2 4 4" stroke="#fff" stroke-width="1.2" fill="none"/></svg>www.halvernrealty.com</li>
    </ul>

    <footer class="footer-band">421, Address line goes&nbsp; here Country Name, 45452</footer>
  </main>
</body>
</html>
```